I am a general contractor in Portland, Or. I would like a clean and simple design layout, maybe using the "didot" font, blue and dark bronze in colors are preferred. On one side of the card, it would be nice to have a logo(attached photo) and business name(KTW Construction). I don't need my job title on the card, just some thing along the lines of "gordon pike, general contractor". Thanks much.

Target Market(s)

Adults from 30-55 years old. Middle to upper class.

Industry/Entity Type

Contractor

Contact Information for Business Card

KTW Construction
Gordon L. Pike
2843 NE 71st Ave.
Portland, Or. 97288
541.555.0187

Font styles to use
Other font styles liked:
• didot

Colors
3277b5
7f7f7f

Requirements
Should not have
• Too much going on.

```html
<!DOCTYPE html>
<html lang="en">
<head>
<meta charset="utf-8">
<title>KTW Construction – Business Card</title>
<link rel="stylesheet" href="https://fonts.googleapis.com/css2?family=GFS+Didot&display=swap">
<style>
  :root {
    --backdrop: #e6e7e9;
    --card: #ffffff;
    --navy: #1f3f8f;
    --blue-deep: #1a5aa6;
    --blue-bright: #2f8bd0;
    --sky: #3a9bd8;
    --stripe-grey: #8c8c8c;
    --ink-light: #ffffff;
    --didot: "GFS Didot", "Didot", serif;
  }
  * { box-sizing: border-box; margin: 0; padding: 0; }
  html, body {
    width: 1200px; height: 771px; overflow: hidden;
    background: var(--backdrop);
  }
  .stage {
    width: 1200px; height: 771px;
    display: flex; align-items: center; justify-content: center; gap: 60px;
  }
  .card {
    position: relative;
    width: 520px; height: 297px;
    background: var(--card);
    overflow: hidden;
    box-shadow: 0 6px 18px rgba(0,0,0,0.18);
  }
  .card-art { position: absolute; inset: 0; }

  /* Front */
  .brand {
    position: absolute; top: 24px; left: 250px;
    display: flex; align-items: center; gap: 14px;
  }
  .brand-dot {
    width: 46px; height: 46px; border-radius: 50%;
    background: var(--sky); flex: none;
  }
  .brand-name {
    font-family: var(--didot); font-weight: 400;
    font-size: 29px; line-height: 1.0; color: var(--navy);
  }
  .contact {
    position: absolute; top: 102px; left: 22px;
    list-style: none;
    font-family: var(--didot); font-size: 10.5px;
    color: var(--ink-light); letter-spacing: 0.5px;
  }
  .contact li { display: flex; align-items: center; gap: 7px; height: 14px; }
  .contact li.indent { padding-left: 15px; }
  .contact-icon { width: 8px; height: 8px; flex: none; }
  .person {
    position: absolute; right: 24px; bottom: 22px;
    text-align: right; color: var(--ink-light);
    font-family: var(--didot);
  }
  .person-name { font-size: 14px; letter-spacing: 2px; text-transform: uppercase; }
  .person-title { font-size: 9.5px; letter-spacing: 2.5px; text-transform: uppercase; margin-top: 4px; }

  /* Back */
  .back-mark {
    position: absolute; left: 40px; top: 50%; transform: translateY(-50%);
    display: flex; align-items: center; gap: 26px;
  }
  .back-dot {
    width: 180px; height: 180px; border-radius: 50%;
    background: var(--sky); flex: none;
  }
  .back-name {
    font-family: var(--didot); font-weight: 400;
    font-size: 38px; line-height: 1.05; color: var(--navy);
  }
</style>
</head>
<body>
<main class="stage">

  <section class="card card-front" aria-label="Card front">
    <svg class="card-art" viewBox="0 0 520 297" aria-hidden="true">
      <defs>
        <linearGradient id="bandFill" x1="0" y1="0" x2="1" y2="1">
          <stop offset="0" stop-color="#1a5aa6"/>
          <stop offset="0.5" stop-color="#2f8bd0"/>
          <stop offset="1" stop-color="#1a5aa6"/>
        </linearGradient>
      </defs>
      <path d="M0,72 C160,62 350,102 520,210 L520,219 C340,112 160,76 0,83 Z" fill="#8c8c8c"/>
      <path d="M0,90 C150,82 330,122 520,230 L520,297 L0,297 Z" fill="url(#bandFill)"/>
    </svg>

    <div class="brand">
      <span class="brand-dot"></span>
      <div class="brand-name">KTW<br>Construction</div>
    </div>

    <ul class="contact">
      <li><svg class="contact-icon" viewBox="0 0 8 8"><path d="M4,0 C6,0 7,1.5 7,3 C7,5 4,8 4,8 C4,8 1,5 1,3 C1,1.5 2,0 4,0 Z" fill="#fff"/></svg>2843 NE 71st Ave.</li>
      <li class="indent">Portland, Or. 97288</li>
      <li><svg class="contact-icon" viewBox="0 0 8 8"><circle cx="4" cy="4" r="4" fill="#fff"/><path d="M2.5,2 L3.5,2 L4,3.2 L3.4,3.8 C3.8,4.5 4.2,4.9 4.8,5.2 L5.4,4.6 L6.4,5.1 L6.2,6 C4.5,6 2.5,4.2 2.5,2 Z" fill="#1a5aa6"/></svg>541.555.0187</li>
      <li><svg class="contact-icon" viewBox="0 0 8 8"><circle cx="4" cy="4" r="4" fill="#fff"/><rect x="2.5" y="1.5" width="3" height="5" rx="0.6" fill="#1a5aa6"/></svg>541.555.0142</li>
      <li><svg class="contact-icon" viewBox="0 0 8 8"><circle cx="4" cy="4" r="4" fill="#fff"/><rect x="2" y="2.5" width="4" height="3" fill="#1a5aa6"/></svg>541.555.0199</li>
      <li><svg class="contact-icon" viewBox="0 0 8 8"><circle cx="4" cy="4" r="4" fill="#fff"/><path d="M2,2.6 L6,2.6 L6,5.4 L2,5.4 Z M2,2.6 L4,4.2 L6,2.6" fill="none" stroke="#1a5aa6" stroke-width="0.6"/></svg>gordon@ktwbuilds.com</li>
      <li class="indent">www.ktwbuilds.com</li>
    </ul>

    <div class="person">
      <p class="person-name">Gordon L. Pike</p>
      <p class="person-title">General Contractor</p>
    </div>
  </section>

  <section class="card card-back" aria-label="Card back">
    <div class="back-mark">
      <span class="back-dot"></span>
      <div class="back-name">KTW<br>Construction</div>
    </div>
  </section>

</main>
</body>
</html>
```